"Harbor Builders" is a residential building company and needs a new business card design and may re

We would like a redesign based on the existing logo, and would like to see a new font as well. We are bespoke home builders who build sustainable energy efficient homes.

Industry/Entity Type

Construction

Contact Information for Business Card

Business card size 40mm x 90mm

Colors

Designer to choose colors to be used in the design.

```html
<!DOCTYPE html>
<html lang="en">
<head>
<meta charset="utf-8">
<title>Harbor Builders – Business Cards</title>
<link rel="stylesheet" href="https://fonts.googleapis.com/css2?family=Source+Sans+3:wght@400;600;700&display=swap">
<style>
  :root {
    --backdrop: #9b9b9b;
    --card-light: #e6e6e8;
    --card-dark: #050607;
    --ink: #2a2a2a;
    --ink-soft: #3f3f3f;
    --accent: #a4be2e;
    --logo-light: #e9e9eb;
  }
  * { box-sizing: border-box; margin: 0; padding: 0; }
  html, body {
    width: 1105px;
    height: 1200px;
    overflow: hidden;
    background: var(--backdrop);
    font-family: "Source Sans 3", "Myriad Pro", Arial, sans-serif;
  }
  .canvas { position: relative; width: 1105px; height: 1200px; }
  .card {
    position: absolute;
    left: 182px;
    width: 747px;
    height: 427px;
  }
  .card--front { top: 119px; background: var(--card-light); color: var(--ink-soft); text-align: center; }
  .card--back { top: 636px; background: var(--card-dark); }

  .front-brand {
    position: absolute;
    top: 200px;
    left: 0; right: 0;
    margin-top: -200px;
    padding-top: 70px;
    font-size: 30px;
    font-weight: 600;
    color: var(--accent);
    letter-spacing: 0.5px;
    line-height: 1;
  }
  .contact {
    position: absolute;
    top: 176px;
    left: 0; right: 0;
  }
  .contact__name {
    font-size: 28px;
    font-weight: 700;
    color: var(--ink);
    line-height: 1;
    margin-bottom: 18px;
  }
  .contact__company { font-size: 17px; font-weight: 600; line-height: 22px; }
  .contact__line { font-size: 17px; line-height: 22px; }
  .contact__reg { font-size: 14.5px; line-height: 24px; letter-spacing: -0.2px; }
  .contact__reg b { font-weight: 700; }
  .contact__group { margin-top: 6px; }

  .back-brand {
    position: absolute;
    top: 0; bottom: 0; left: 0; right: 0;
    display: flex;
    align-items: center;
    justify-content: center;
    gap: 30px;
  }
  .back-brand__square { width: 86px; height: 86px; background: var(--accent); }
  .back-brand__name {
    font-size: 60px;
    font-weight: 600;
    color: var(--logo-light);
    line-height: 1;
    letter-spacing: 0.5px;
  }
</style>
</head>
<body>
<main class="canvas">
  <section class="card card--front" aria-label="Business card front">
    <p class="front-brand">harbor builders</p>
    <div class="contact">
      <p class="contact__name">Daniel Moretti</p>
      <p class="contact__company">Harbor Builders Pty Ltd</p>
      <p class="contact__line">PO Box 4120 Eastgate, LPO Kingsford WA 6190</p>
      <p class="contact__reg"><b>Registration:</b> 40871 &nbsp;<b>ABN:</b> 52 604 319 778</p>
      <div class="contact__group">
        <p class="contact__line">0400 555 017</p>
        <p class="contact__line">daniel@harborbuilders.com.au</p>
        <p class="contact__line">www.harborbuilders.com.au</p>
      </div>
    </div>
  </section>

  <section class="card card--back" aria-label="Business card back">
    <div class="back-brand">
      <span class="back-brand__square"></span>
      <p class="back-brand__name">harbor builders</p>
    </div>
  </section>
</main>
</body>
</html>
```